International business needs business cards

Our company, DRV Ventures Inc. is in the business of supplying a range construction products with particular emphasis on CEMENT. We have developed our own brand - TORVAN SUPPLIES - with which to infiltrate the market. We are launching our brand of cement (TORVAN Type IS Cement) into the Caribbean which is unlike anything this market has ever seen. A monopoly has existed here for the past 60-odd years and the market has now opened to allow the importation of other brands and consumers are anxious and ready for change/improvement. We are very excited to be launching and want to make a great first impression. We will be conducting workshops and seminars (from government level to the hardware store owners) and we want our business card to give us the strong, confident introduction that we need.

Target Market(s)

construction; builders; engineers; home owners

Industry/Entity Type

Construction

Contact Information for Business Card

Marisol Depree
CEO
cell # 1 555 4180736
Ground floor,Lindell Plaza Suite 2734
George Town,Grand Cayman
Cayman Islands,KY1-4823
EMAIL: m.depree@drvventuresinc.example
web site drvventuresinc.example

COMPANY: skype info drv.ventures.example

second card
Yvette Brannock-Depree
CFO
CELL# 1 555 607 3941
George Town,Grand Cayman
Cayman Islands,KY1-4823
EMAIL: y.brannockdepree@drvventuresinc.example
website drvventuresinc.example

Requirements
Must have
• Business cards must display BOTH logos - DRV is the company and TORVAN is the brand.

```html
<!DOCTYPE html>
<html lang="en">
<head>
<meta charset="utf-8">
<title>DRV Ventures Inc. — Business Card</title>
<link href="https://fonts.googleapis.com/css2?family=Open+Sans:wght@400;600;700&display=swap" rel="stylesheet">
<style>
  :root {
    --backdrop: #d9d5d1;
    --card: #121212;
    --card-edge: #1d1d1d;
    --brand-red: #8e1a1c;
    --name-red: #b3232a;
    --text-light: #e9e9e9;
    --text-muted: #9a9a9a;
    --divider: #5a5a5a;
    --emblem: #3a3a3a;
  }
  * { box-sizing: border-box; margin: 0; padding: 0; }
  html, body { width: 1200px; height: 814px; overflow: hidden; }
  body {
    background: var(--backdrop);
    font-family: "Open Sans", Arial, sans-serif;
    position: relative;
  }
  .card {
    position: absolute;
    top: 252px;
    width: 540px;
    height: 309px;
    background: var(--card);
    border: 1px solid var(--card-edge);
    border-radius: 3px;
    box-shadow: 0 10px 28px rgba(0,0,0,0.28);
  }
  .card--contact { left: 45px; }
  .card--brand { left: 615px; }

  /* contact side */
  .company-mark {
    position: absolute;
    left: 46px;
    top: 92px;
    width: 150px;
    display: flex;
    flex-direction: column;
    align-items: center;
    gap: 14px;
  }
  .company-mark__square {
    width: 112px;
    height: 112px;
    background: var(--brand-red);
    border: 1px solid #6c1213;
  }
  .company-mark__name {
    color: var(--text-light);
    font-weight: 700;
    font-size: 15px;
    letter-spacing: 0.5px;
    white-space: nowrap;
  }
  .divider {
    position: absolute;
    left: 238px;
    top: 44px;
    width: 1px;
    height: 220px;
    background: linear-gradient(to bottom, transparent, var(--divider) 20%, var(--divider) 80%, transparent);
  }
  .contact {
    position: absolute;
    left: 262px;
    top: 46px;
    color: var(--text-light);
    font-size: 14px;
    line-height: 19px;
  }
  .contact__name {
    color: var(--name-red);
    font-size: 17px;
    font-weight: 600;
    line-height: 22px;
  }
  .contact__role { margin-bottom: 2px; }
  .contact__lines { margin-top: 8px; list-style: none; }
  .contact__lines li { display: flex; align-items: center; gap: 9px; }
  .contact__lines svg { width: 12px; height: 12px; flex: none; fill: var(--name-red); }

  /* brand side */
  .brand-emblem {
    position: absolute;
    left: 70px;
    top: 78px;
    width: 160px;
    height: 130px;
    border-radius: 6px;
    background: radial-gradient(ellipse at center, #4a4a4a 0%, var(--emblem) 45%, var(--card) 78%);
    display: flex;
    align-items: center;
    justify-content: center;
  }
  .brand-emblem__name {
    color: var(--text-muted);
    font-weight: 700;
    font-size: 15px;
    letter-spacing: 2px;
    text-align: center;
    line-height: 20px;
  }
  .company-lockup {
    position: absolute;
    left: 270px;
    top: 100px;
    display: flex;
    align-items: center;
    gap: 10px;
  }
  .company-lockup__square {
    width: 62px;
    height: 62px;
    background: var(--brand-red);
    border: 2px solid #f2f2f2;
  }
  .company-lockup__name {
    color: var(--text-light);
    font-weight: 700;
    font-size: 19px;
    line-height: 22px;
  }
  .web {
    position: absolute;
    left: 0;
    right: 0;
    top: 238px;
    text-align: center;
    color: var(--text-muted);
    font-size: 12px;
    letter-spacing: 2px;
  }
</style>
</head>
<body>
  <section class="card card--contact">
    <div class="company-mark">
      <div class="company-mark__square"></div>
      <span class="company-mark__name">DRV Ventures Inc.</span>
    </div>
    <div class="divider"></div>
    <div class="contact">
      <p class="contact__name">Marisol Depree</p>
      <p class="contact__role">CEO</p>
      <p>Ground floor<br>Lindell Plaza Suite 2734<br>George Town,Grand Cayman<br>Cayman Islands,KY1-4823</p>
      <ul class="contact__lines">
        <li><svg viewBox="0 0 12 12"><path d="M3 0h6a1 1 0 0 1 1 1v10a1 1 0 0 1-1 1H3a1 1 0 0 1-1-1V1a1 1 0 0 1 1-1zm0 1.5v8h6v-8zm3 8.7a.7.7 0 1 0 0 .1z"/></svg>1 555 4180736</li>
        <li><svg viewBox="0 0 12 12"><path d="M0 2h12v8H0zm1 1v.4l5 3.4 5-3.4V3zm0 1.6V9h10V4.6L6 8z"/></svg>m.depree@drvventuresinc.example</li>
        <li><svg viewBox="0 0 12 12"><circle cx="6" cy="6" r="6"/></svg>drvventuresinc.example</li>
      </ul>
    </div>
  </section>

  <section class="card card--brand">
    <div class="brand-emblem" role="img" aria-label="TORVAN SUPPLIES brand emblem">
      <span class="brand-emblem__name">TORVAN<br>SUPPLIES</span>
    </div>
    <div class="company-lockup">
      <div class="company-lockup__square"></div>
      <span class="company-lockup__name">DRV<br>Ventures Inc.</span>
    </div>
    <p class="web">www.drvventuresinc.example</p>
  </section>
</body>
</html>
```